Gobal construction supply company needs new business card design

I need a business card design for my global supply company using an existing logo. i will be looking to print these on rounded corner cards with the black background version of my logo on the back. on the front white background, my logo again and my simple details.

```html
<!DOCTYPE html>
<html lang="en">
<head>
<meta charset="utf-8">
<title>Meridian Supply Works – Business Card</title>
<link rel="stylesheet" href="https://fonts.googleapis.com/css2?family=Montserrat:wght@400;500;600;700&display=swap">
<style>
  :root {
    --bg: #4a4a4c;
    --card-black: #111112;
    --card-white: #ffffff;
    --ink: #161616;
    --red: #e3101a;
    --white: #ffffff;
  }
  * { box-sizing: border-box; margin: 0; padding: 0; }
  html, body { width: 1200px; height: 1000px; overflow: hidden; }
  body {
    background: var(--bg);
    font-family: "Montserrat", sans-serif;
    position: relative;
  }
  .card {
    position: absolute;
    width: 700px;
    height: 400px;
    border-radius: 28px;
  }
  .card-back {
    left: 420px; top: 70px;
    background: var(--card-black);
  }
  .card-back .brand {
    position: absolute;
    right: 60px; bottom: 60px;
    display: flex; align-items: center; gap: 12px;
  }
  .card-back .brand-name {
    color: var(--white);
    font-weight: 700;
    font-size: 26px;
    letter-spacing: 0.5px;
  }
  .brand-dot {
    width: 22px; height: 22px; border-radius: 50%;
    background: var(--red);
    flex: none;
  }
  .card-front {
    left: 80px; top: 520px;
    background: var(--card-white);
    display: flex; align-items: center;
  }
  .front-brand {
    width: 370px;
    padding-left: 40px;
    display: flex; align-items: center; gap: 12px;
  }
  .front-brand .brand-name {
    color: var(--ink);
    font-weight: 700;
    font-size: 26px;
    line-height: 1.15;
    letter-spacing: 0.3px;
  }
  .divider {
    width: 2px; height: 200px;
    background: var(--red);
  }
  .details {
    padding-left: 34px;
    color: var(--ink);
  }
  .person-name {
    color: var(--red);
    font-weight: 700;
    font-size: 20px;
  }
  .person-role {
    font-size: 13px;
    font-weight: 500;
    margin-top: 2px;
  }
  .address {
    font-size: 13.5px;
    font-weight: 600;
    line-height: 1.35;
    margin-top: 22px;
  }
  .contact-list { list-style: none; margin-top: 8px; }
  .contact-list li {
    display: flex; align-items: center; gap: 10px;
    font-size: 15px; font-weight: 600;
    line-height: 1.45;
  }
  .contact-list svg { width: 13px; height: 13px; flex: none; }
</style>
</head>
<body>
  <section class="card card-back" aria-label="Card back">
    <div class="brand">
      <span class="brand-name">Meridian Supply Works</span>
      <span class="brand-dot"></span>
    </div>
  </section>

  <section class="card card-front" aria-label="Card front">
    <div class="front-brand">
      <span class="brand-name">MERIDIAN<br>SUPPLY WORKS</span>
      <span class="brand-dot"></span>
    </div>
    <div class="divider"></div>
    <div class="details">
      <p class="person-name">DANIEL CARTER</p>
      <p class="person-role">Managing Director</p>
      <p class="address">1520 Ridge Lane,<br>Fairview City, OK 73100</p>
      <ul class="contact-list">
        <li>
          <svg viewBox="0 0 16 16"><path fill="var(--red)" d="M3 1l3 3-1.5 2a9 9 0 005.5 5.5L12 10l3 3-2 2C7 15 1 9 1 3z"/></svg>
          +1 (555) 010 2040
        </li>
        <li>
          <svg viewBox="0 0 16 16"><rect x="4" y="1" width="8" height="14" rx="1.5" fill="none" stroke="var(--red)" stroke-width="1.6"/><circle cx="8" cy="12.5" r="0.9" fill="var(--red)"/></svg>
          +1 (555) 010 2041
        </li>
        <li>
          <svg viewBox="0 0 16 16"><rect x="1" y="3" width="14" height="10" rx="1" fill="var(--red)"/><path d="M1.5 3.5L8 9l6.5-5.5" fill="none" stroke="#fff" stroke-width="1.3"/></svg>
          dan@meridiansw.com
        </li>
        <li>
          <svg viewBox="0 0 16 16"><circle cx="8" cy="8" r="7" fill="var(--red)"/><path d="M1 8h14M8 1c-3 3.5-3 10.5 0 14M8 1c3 3.5 3 10.5 0 14" fill="none" stroke="#fff" stroke-width="1"/></svg>
          www.meridiansw.com
        </li>
      </ul>
    </div>
  </section>
</body>
</html>
```